Create Website for new company called "Verdale Lodge 37"

Verdale Lodge 37 is a new business situated in Southwestern Colorado. We are creating a business that will rent out spaces where clients can grow their own marijuana. Picture a large green house with partitioned spaces that are secured by a lock. Best way to envision this would be to think of a storage business that rents out storage rooms. The difference is that we will be having the units inside a green house ( for growing purposes) Picture a small area that is secured by locks, Picture an area that has the ability to provide state of the art security, cameras etc. We want to focus our efforts on professionals, blue collar workers and end users of marijuana. Our emphasis is in the area of assisting those whom wish to grow their own plants. We want to provide them a safe facility in which to do that. . Keep in mind that we also build custom grow rooms at clients homes and provide a grow pod (lease these) where a small grow unit will be delivered and picked up from our clients whom want to lease a unit for a short amount of time. We have a business card ( just designed) and will send that information to those whom express an interests in this project. We want to be able to sign people up for our services by entering an agreement and signing the agreement while on the internet. We want to provide our services to those whom consume recreational and medical marijuana. This site will need to gather information I.e email addresses so that we can followup with offers. This is a tremendous opportunity for the right designer. We will be creating many more websites as other states come on line and make marijuana legal to consume. Use the business card model for a point of reference of how we envision the concept. That is a business card we just recently printed. The hands and the plant is our logo so far. Open to suggestions. There will be three levels of service. Bronze, Silver, Gold or Platinum. We will also have a retail biz down the road but not at the present time.

Target Market(s)

Ages 21-60

Industry/Entity Type

Medical

Logo Text

Verdale Lodge 37.

Number of Pages Required

5+ page

Requirements
Must have
• Clean appearance not to busy , easily navigable from link to link, page to page. Must have ability down the road to enter into a contractual agreement via the website. Must use our provided logo and example of that is on our business card that will be uploaded here shortly. We would like to have the colors that are on the business card however if you have suggestions or color schemes that you want us to consider that is okay.
Nice to have
• Nice to have a animation of seed to weed and how clients can save a tremendous amount of money growing their own cannabis. Nice to have testimonial page or feedback page. Have a membership component to website,
Should not have
• No flashing lights, etc. Not to busy in terms of animations.

```html
<!DOCTYPE html>
<html lang="en">
<head>
<meta charset="utf-8">
<title>Verdale Lodge 37</title>
<link rel="stylesheet" href="https://fonts.googleapis.com/css2?family=Roboto+Condensed:wght@400;700&family=Lato:ital,wght@0,400;0,700;1,400&display=swap">
<style>
:root{
  --green:#0b8a3e;
  --green-dark:#06702f;
  --green-light:#17a24d;
  --ink:#333;
  --muted:#6b6b6b;
  --paper:#f6f6f6;
  --footer:#333333;
  --footer-panel:#4f4f4f;
  --line:#cfcfcf;
  --white:#fff;
}
*{box-sizing:border-box;margin:0;padding:0}
html,body{width:780px;height:1200px;overflow:hidden}
body{font-family:"Lato",sans-serif;color:var(--ink);background:var(--white)}
.page{position:relative;width:780px;height:1200px;overflow:hidden;background:var(--paper)}
.abs{position:absolute}
.nowrap{white-space:nowrap}

/* top bar */
.topbar{left:0;top:0;width:780px;height:52px;background:linear-gradient(#14a04c,var(--green-dark))}
.topbar .phone{left:85px;top:16px;color:var(--white);font-size:17px;display:flex;align-items:center;gap:6px}
.social{display:flex;gap:6px}
.social span{width:22px;height:22px;border-radius:50%;background:var(--white);display:block}
.topbar .social{left:590px;top:15px}

/* nav */
.nav{left:0;top:52px;width:780px;height:36px;background:var(--white);border-bottom:1px solid #ddd}
.nav a{position:absolute;top:6px;height:25px;line-height:25px;font-family:"Roboto Condensed",sans-serif;font-size:10.5px;color:#333;text-decoration:none;text-transform:uppercase;padding:0 9px;border-right:1px solid #ccc;white-space:nowrap}
.nav a.active{background:var(--green);color:var(--white);border:0;width:58px;text-align:center;padding:0}
.brand-badge{left:292px;top:12px;width:196px;height:114px;border-radius:50%;background:var(--white);border:4px solid #e6efe8;display:flex;align-items:center;justify-content:center;gap:6px}
.brand-badge .dot{width:12px;height:12px;border-radius:50%;background:var(--green)}
.brand-name{font-family:"Roboto Condensed",sans-serif;font-weight:700;font-size:20px;color:#3a3a3a;white-space:nowrap}

/* hero */
.hero{left:0;top:88px;width:780px;height:311px;background:radial-gradient(ellipse at 40% 40%,#7fb04a 0%,#3f7a2a 45%,#1e3d17 100%)}
.hero .arrow{top:140px}
.hero .caption{left:417px;top:180px;width:278px;height:67px;background:rgba(0,0,0,.45);color:var(--white);font-family:"Roboto Condensed",sans-serif;font-size:19.5px;letter-spacing:-.3px;line-height:29px;text-align:right;padding:5px 14px 0 0;white-space:nowrap}

/* service cards */
.card{top:363px;width:188px;height:214px;background:var(--white);border:1px solid #bdbdbd;border-radius:5px;box-shadow:0 10px 8px -8px rgba(0,0,0,.25)}
.card h3{height:35px;background:linear-gradient(#17a24d,var(--green-dark));border-radius:4px 4px 0 0;color:var(--white);font-family:"Roboto Condensed",sans-serif;font-weight:400;font-size:15px;line-height:37px;padding-left:13px}
.card .thumb{margin:11px 9px 0;height:72px;border:3px solid #666}
.card p{margin:10px 10px 0;font-size:8.6px;line-height:14.5px;color:var(--muted);white-space:nowrap;letter-spacing:-.1px}
.more{display:inline-block;font-size:8px;font-weight:700;color:#333;text-decoration:underline;text-transform:uppercase;white-space:nowrap}
.card .more{margin:3px 10px 0}

/* welcome */
.welcome{left:0;top:607px;width:780px;height:183px;background:linear-gradient(#0e9444,var(--green-dark))}
.video{left:85px;top:18px;width:188px;height:146px;background:linear-gradient(#2f5a24,#4f8a36);overflow:hidden}
.video .controls{left:0;bottom:0;width:188px;height:19px;background:#111;color:#ddd;font-size:7px}
.welcome h2{left:296px;top:17px;color:var(--white);font-family:"Roboto Condensed",sans-serif;font-weight:400;font-size:18.5px}
.welcome .rule{left:296px;top:43px;width:399px;height:1px;background:rgba(255,255,255,.5)}
.welcome p{left:296px;color:var(--white);font-size:8.6px;line-height:14.5px;white-space:nowrap;letter-spacing:-.15px}
.welcome .more{color:var(--white)}

/* testimonial & news */
.mid{left:0;top:790px;width:780px;height:225px;background:linear-gradient(#f7f7f7,#dedede)}
.sec-title{font-family:"Roboto Condensed",sans-serif;font-size:15px;color:#333;display:flex;align-items:center;gap:8px}
.sec-rule{height:1px;background:#888}
.quote{left:85px;top:64px;width:281px;height:108px;background:#666;border-radius:3px;color:var(--white);font-style:italic;font-size:8.5px;line-height:15.5px;padding:14px 10px 0 19px;white-space:nowrap;letter-spacing:-.1px}
.quote::after{content:"";position:absolute;left:26px;bottom:-12px;border-left:20px solid #666;border-bottom:12px solid transparent}
.news-item{left:414px;width:300px;font-size:8.4px;line-height:14px;color:var(--muted);padding-left:13px;white-space:nowrap;letter-spacing:-.1px}
.news-item .date{font-weight:700;color:#333;position:relative}
.news-item .date::before{content:"";position:absolute;left:-13px;top:3px;width:8px;height:7px;background:#999}
.news-item h4{font-size:9px;color:#444;font-weight:700}

/* footer */
.footer{left:0;top:1015px;width:780px;height:185px;background:var(--footer);color:#ddd}
.quote-panel{left:85px;top:3px;width:188px;height:182px;background:var(--footer-panel);padding:0 12px}
.quote-panel h3{font-family:"Roboto Condensed",sans-serif;font-weight:400;font-size:16px;color:var(--white);margin-top:11px;display:flex;align-items:center;gap:8px}
.field{width:164px;height:22px;border:1px solid #777;background:#595959;font-size:7px;color:#aaa;padding:6px 7px;margin-top:4px}
.btn{background:var(--green);color:var(--white);font-size:10.5px;display:flex;align-items:center;justify-content:center}
.footer h4{font-family:"Roboto Condensed",sans-serif;font-weight:400;font-size:13px;color:var(--white)}
.footer .small{font-size:8.5px;line-height:13.5px;color:#ddd}
</style>
</head>
<body>
<div class="page">

  <header>
    <div class="abs topbar">
      <div class="abs phone">
        <svg width="18" height="18" viewBox="0 0 18 18"><circle cx="9" cy="9" r="8" fill="none" stroke="#fff" stroke-width="1.5"/><path d="M6 5l2 2-1 1c.6 1.3 1.7 2.4 3 3l1-1 2 2-1.5 1.5C8.5 13 5 9.5 4.5 6.5z" fill="#fff"/></svg>
        <span>+123-555-0142</span>
      </div>
      <div class="abs social" aria-label="Social links"><span></span><span></span><span></span><span></span></div>
    </div>
    <nav class="abs nav">
      <a class="active" href="#" style="left:85px">Home</a>
      <a href="#" style="left:152px">About Us</a>
      <a href="#" style="left:226px;border-right:0">Services</a>
      <a href="#" style="left:496px">Facilities</a>
      <a href="#" style="left:556px">Testimonial</a>
      <a href="#" style="left:627px;border-right:1px solid #e8a23a">Contact Us</a>
    </nav>
    <div class="abs brand-badge"><span class="dot"></span><span class="brand-name">Verdale Lodge 37</span></div>
  </header>

  <section class="abs hero" role="img" aria-label="Close-up photograph of a green cannabis plant">
    <svg class="abs arrow" style="left:55px" width="32" height="32" viewBox="0 0 32 32"><circle cx="16" cy="16" r="14" fill="rgba(0,0,0,.25)" stroke="#ddd" stroke-width="2"/><path d="M18 10l-6 6 6 6" fill="none" stroke="#fff" stroke-width="2"/></svg>
    <svg class="abs arrow" style="left:694px" width="32" height="32" viewBox="0 0 32 32"><circle cx="16" cy="16" r="14" fill="rgba(0,0,0,.25)" stroke="#ddd" stroke-width="2"/><path d="M14 10l6 6-6 6" fill="none" stroke="#fff" stroke-width="2"/></svg>
    <div class="abs caption">Lorem ipsum dolor sit amet,<br>consectetuer adipiscing elit, sed</div>
  </section>

  <section>
    <article class="abs card" style="left:85px">
      <h3>FOR LEASE</h3>
      <div class="thumb" role="img" aria-label="Photo of a for-lease sign in front of a house" style="background:linear-gradient(90deg,#9fb3c7,#c9d6c2 60%,#8aa06d)"></div>
      <p>Lorem ipsum dolor sit ametuer adipiscingi<br>elit, sed diam nmy nibh euismod tincidunt<br>ut laoreet dolore magna am erat visi enim<br>ad minim veniam, quis nostrud exerci</p>
      <a class="more" href="#">Read more »</a>
    </article>
    <article class="abs card" style="left:296px">
      <h3>FOR LOCK</h3>
      <div class="thumb" role="img" aria-label="Photo of a padlock on a weathered door" style="background:linear-gradient(90deg,#3b4a3a,#9a9a90 55%,#d8d8d0)"></div>
      <p>Lorem ipsum dolor sit ametuer adipiscingi<br>elit, sed diam nmy nibh euismod tincidunt<br>ut laoreet dolore magna am erat visi enim<br>ad minim veniam, quis nostrud exerci</p>
      <a class="more" href="#">Read more »</a>
    </article>
    <article class="abs card" style="left:507px">
      <h3>FOR CAMERA</h3>
      <div class="thumb" role="img" aria-label="Photo of a security camera on a warm background" style="background:linear-gradient(90deg,#d9b48a,#a9713f 55%,#d8a877)"></div>
      <p>Lorem ipsum dolor sit ametuer adipiscingi<br>elit, sed diam nmy nibh euismod tincidunt<br>ut laoreet dolore magna am erat visi enim<br>ad minim veniam, quis nostrud exerci</p>
    </article>
  </section>

  <section class="abs welcome">
    <div class="abs video">
      <div class="abs" style="inset:0 0 19px 0" role="img" aria-label="Video still of a grower tending cannabis plants indoors"></div>
      <svg class="abs" style="left:82px;top:55px" width="24" height="24" viewBox="0 0 24 24"><circle cx="12" cy="12" r="11" fill="#fff"/><path d="M9.5 7l7 5-7 5z" fill="#333"/></svg>
      <div class="abs controls">
        <svg class="abs" style="left:8px;top:5px" width="8" height="9"><path d="M0 0l8 4.5L0 9z" fill="#ddd"/></svg>
        <span class="abs" style="left:28px;top:6px">04:59</span>
        <span class="abs" style="left:52px;top:8px;width:72px;height:3px;background:#555"></span>
        <span class="abs" style="left:52px;top:8px;width:55px;height:3px;background:#888"></span>
        <span class="abs" style="left:128px;top:6px">10:35</span>
        <svg class="abs" style="left:151px;top:5px" width="10" height="9"><path d="M0 3h3l3-3v9L3 6H0z" fill="#ddd"/></svg>
        <svg class="abs" style="left:171px;top:5px" width="9" height="9"><path d="M0 0l9 9M6 9h3V6M3 0H0v3" stroke="#ddd" fill="none"/></svg>
      </div>
    </div>
    <h2 class="abs">Welcome To Verdale Lodge 37</h2>
    <div class="abs rule"></div>
    <p class="abs" style="top:55px">Lorem ipsum dolor sit amet, consectetuer adipiscing elit, sed diam nonummy nibh euismod ut laoreet<br>dolore magna aliquam erat volutpat. Ut wisi enim ad minim veniam, quis nostrud etation ullamcorper<br>suscipit lobortis nisl ut aliquip ex ea commodo consequat.</p>
    <p class="abs" style="top:113px">Duis autem vel eum iriure dor in hendrerit in vulputate velit esse molestie  vel illum dolore eu feugiat<br>nulla facilisro eros et accumsan et iusto odio dignissim qui blandit praesent luptatum zzril.</p>
    <a class="abs more" href="#" style="left:296px;top:148px">Read more »</a>
  </section>

  <section class="abs mid">
    <div class="abs sec-title" style="left:87px;top:21px">
      <svg width="19" height="17" viewBox="0 0 19 17"><path d="M1 1h11v7H6l-3 3V8H1z" fill="var(--green)"/><path d="M14 5h4v7h-2v3l-3-3H8v-2h6z" fill="var(--green)"/></svg>
      Client Testimonial
    </div>
    <div class="abs sec-rule" style="left:85px;top:47px;width:281px"></div>
    <blockquote class="abs quote">
      <svg class="abs" style="left:18px;top:15px" width="14" height="12"><path d="M0 12V6l4-6h2L4 6h2v6zM8 12V6l4-6h2l-2 6h2v6z" fill="#ccc"/></svg>
      <span style="padding-left:18px">Lorem ipsum dolor sit amet, consectetuer adipi sed diam nony</span><br>nibh euismod ut laoreet dolore magna aliquam erat volut wisi enim<br>ad minim veniam, quis nostrud etation ullamcorpecipit lobortis nisl<br>ut aliquip ex ea commodo consequatquis autem vel eum iriure dor in<br>hendrerit in vulputate velit esse molestie  vel illum dolore
      <svg style="vertical-align:middle;margin-left:3px" width="14" height="12"><path d="M14 0v6l-4 6H8l2-6H8V0zM6 0v6l-4 6H0l2-6H0V0z" fill="#ccc"/></svg>
    </blockquote>
    <div class="abs" style="left:141px;top:178px;font-size:9.5px;font-weight:700">Mr. Nisl Ut Aliquip</div>
    <div class="abs" style="left:390px;top:30px;width:1px;height:150px;background:linear-gradient(transparent,#bbb,transparent)"></div>

    <div class="abs sec-title" style="left:414px;top:21px">
      <svg width="20" height="16" viewBox="0 0 20 16"><path d="M1 5h4l9-5v16L5 11H1z" fill="var(--green)"/><path d="M4 11l2 5h3l-2-5z" fill="var(--green)"/></svg>
      Latest News
    </div>
    <div class="abs sec-rule" style="left:414px;top:47px;width:281px"></div>
    <div class="abs news-item" style="top:63px">
      <div class="date">14-March-2014</div>
      <h4>Exerci tation ullamcorper suscipit lobortis nisl ut aliquip.</h4>
      <p>Lorem ipsum dolor sit amet, consectetuer adipiscing eli sed di nonmmy<br>nibh euismod tincidunt ut laoreet dolore ma aliquam erat volutpat.</p>
    </div>
    <div class="abs" style="left:414px;top:126px;width:281px;border-top:1px dotted #666"></div>
    <div class="abs news-item" style="top:139px">
      <div class="date">14-March-2014</div>
      <h4>Mullamcorper suscipit lobortis nisl ut aliquip.</h4>
      <p>nibh euismod tincidunt ut laoreet dolore ma aliquam erat volutpat.</p>
    </div>
  </section>

  <footer class="abs footer">
    <form class="abs quote-panel">
      <h3>
        <svg width="20" height="15" viewBox="0 0 20 15"><rect x="1" y="1" width="18" height="13" fill="none" stroke="#fff" stroke-width="1.5"/><path d="M1 1l9 7 9-7" fill="none" stroke="#fff" stroke-width="1.5"/></svg>
        Request a Quote
      </h3>
      <div class="field" style="margin-top:9px">Name</div>
      <div class="field">Email</div>
      <div class="field" style="height:42px">Message</div>
      <div class="btn" style="width:49px;height:24px;margin-top:14px">SEND</div>
    </form>

    <h4 class="abs" style="left:296px;top:13px">News Latter Signup</h4>
    <div class="abs" style="left:296px;top:36px;width:185px;height:24px;background:#5a5a5a;font-size:7.5px;color:#eee;padding:8px 9px">Enter Your Email</div>
    <div class="abs btn" style="left:486px;top:36px;width:55px;height:24px">SUBMIT</div>
    <div class="abs" style="left:563px;top:22px;width:1px;height:45px;background:#555"></div>
    <h4 class="abs" style="left:589px;top:13px">Socail Connect</h4>
    <div class="abs social" style="left:590px;top:38px"><span></span><span></span><span></span><span></span></div>

    <div class="abs" style="left:296px;top:77px;width:399px;height:1px;background:#555"></div>
    <svg class="abs" style="left:296px;top:93px" width="9" height="13" viewBox="0 0 9 13"><path d="M4.5 0A4.5 4.5 0 0 0 0 4.5C0 8 4.5 13 4.5 13S9 8 9 4.5A4.5 4.5 0 0 0 4.5 0z" fill="#fff"/><circle cx="4.5" cy="4.5" r="1.6" fill="#333"/></svg>
    <p class="abs small" style="left:314px;top:92px;width:95px;white-space:nowrap">Lorem ipsum dolor sit<br>amet, consectetuer<br>adipiscing eli sed di<br>nonmmy</p>
    <svg class="abs" style="left:428px;top:94px" width="7" height="10"><rect x=".5" y=".5" width="6" height="9" rx="1" fill="none" stroke="#fff"/><rect x="2" y="7" width="3" height="1" fill="#fff"/></svg>
    <span class="abs" style="left:445px;top:93px;font-size:10.5px">123-555-0142</span>
    <svg class="abs" style="left:427px;top:118px" width="10" height="8"><rect x=".5" y=".5" width="9" height="7" fill="none" stroke="#fff"/><path d="M.5 .5l4.5 4 4.5-4" fill="none" stroke="#fff"/></svg>
    <span class="abs" style="left:445px;top:116px;font-size:9.5px">info@verdalelodge.com</span>
    <div class="abs" style="left:563px;top:87px;width:1px;height:50px;background:#555"></div>
    <div class="abs" style="left:584px;top:106px;display:flex;align-items:center;gap:4px">
      <span style="width:8px;height:8px;border-radius:50%;background:var(--green-light)"></span>
      <span class="brand-name" style="font-size:13.5px;color:#cfcfcf">Verdale Lodge 37</span>
    </div>

    <div class="abs" style="left:296px;top:148px;width:399px;height:1px;background:#555"></div>
    <div class="abs" style="left:305px;top:162px;font-size:8.5px">© 2014 Verdale Lodge &nbsp;|&nbsp; All Rights Reserved</div>
  </footer>

</div>
</body>
</html>
```